The Brandwell Firm

We need a new design for our letterhead and envelopes. We are a personal injury and criminal defense firm so we need something modern and clean, but more on the professional/traditional side. Our new logo has two colors and is attached to the file so we need something that works well with those colors/matches the design. The following information needs to be on the letterhead:
Phone: (555) 214-3370
Fax: (555) 214-5186
Toll-Free: (888) 431-2059
Post Office Box 4721
Millbrook, SC 29555-4721
HarmClaimCounsel.example
PalmettoTrialAdvocates.example

Target Market(s)

Clients, government agencies, other law firms

Industry/Entity Type

Legal

Font styles to use
Sans Serif
Other font styles liked:
• Arial

Colors

Designer to choose colors to be used in the design.

Requirements
Must have
• Must look professional and clean, modern
Nice to have
• I would like to see a design that works with the logo but does not distract from the content that will be printed on it
Should not have
• Too many colors or crazy designs.

```html
<!DOCTYPE html>
<html lang="en">
<head>
<meta charset="utf-8">
<title>The Brandwell Firm — Stationery</title>
<link rel="stylesheet" href="https://fonts.googleapis.com/css2?family=Open+Sans:wght@400;600;700&display=swap">
<style>
  :root {
    --navy: #2b2f8f;
    --red: #d11f26;
    --paper: #ffffff;
    --backdrop: #e5e5e5;
    --ink: #333333;
    --rule: #8d8fc4;
  }
  * { box-sizing: border-box; margin: 0; padding: 0; }
  html, body { width: 1200px; height: 1200px; overflow: hidden; }
  body {
    background: var(--backdrop);
    font-family: "Open Sans", Arial, sans-serif;
    color: var(--ink);
    position: relative;
  }
  .sheet { position: absolute; background: var(--paper); overflow: hidden; }
  .wordmark { position: absolute; color: var(--navy); font-weight: 600; white-space: nowrap; letter-spacing: .01em; line-height: 1; }
  .nowrap { white-space: nowrap; }

  /* Letterhead */
  .letterhead { left: 178px; top: 210px; width: 387px; height: 544px; }
  .letterhead .wordmark { left: 24px; top: 55px; font-size: 11px; }
  .letterhead .header-rule { position: absolute; left: 52px; width: 311px; top: 69px; border-top: 1px solid var(--rule); }
  .contact-col {
    position: absolute; top: 49px; font-size: 5.2px; line-height: 8px;
    white-space: nowrap; color: var(--ink);
  }
  .contact-col.address { left: 148px; }
  .contact-col.phones { left: 224px; }
  .contact-col.web { left: 283px; }
  .col-divider { position: absolute; top: 50px; height: 16px; border-left: 1px solid var(--rule); }
  .contact-col .row { display: flex; align-items: center; gap: 3px; }
  .icon { width: 5px; height: 5px; flex: none; }

  /* Folder */
  .folder { left: 623px; top: 186px; width: 455px; height: 571px; }
  .folder .wordmark { left: 0; right: 0; top: 222px; text-align: center; font-size: 23px; }

  /* Business card front */
  .card-front { left: 40px; top: 798px; width: 174px; height: 99px; }
  .card-front .wordmark { left: 10px; top: 30px; font-size: 6px; }
  .card-front .card-rule { position: absolute; left: 70px; right: 11px; top: 36px; border-top: 0.5px solid var(--rule); }
  .card-front .name {
    position: absolute; right: 11px; top: 29px; color: var(--red);
    font-size: 5px; font-weight: 700; text-transform: uppercase; line-height: 6px; white-space: nowrap;
  }
  .card-front .details {
    position: absolute; right: 11px; top: 38px; text-align: right;
    font-size: 3.6px; line-height: 5.5px; white-space: nowrap;
  }
  .card-front .title { color: var(--navy); margin-bottom: 6px; }
  .card-front .gap { margin-top: 2px; }
  .red-text { color: var(--red); font-weight: 600; }

  /* Business card back */
  .card-back { left: 41px; top: 922px; width: 174px; height: 99px; background: var(--red); }
  .card-back .wordmark { right: 11px; top: 80px; color: var(--paper); font-size: 7px; }

  /* Envelope front */
  .envelope-front { left: 255px; top: 812px; width: 429px; height: 206px; }
  .envelope-front .wordmark { left: 19px; top: 54px; font-size: 12px; }
  .envelope-front .return { position: absolute; left: 19px; top: 175px; font-size: 7px; line-height: 8px; white-space: nowrap; }
  .envelope-front .corner { position: absolute; right: 0; bottom: 0; }

  /* Envelope back */
  .envelope-back { left: 724px; top: 811px; width: 428px; height: 209px; }
  .envelope-back .flap { position: absolute; left: 0; top: 0; }
</style>
</head>
<body>

<section class="sheet letterhead" aria-label="Letterhead">
  <span class="wordmark">The Brandwell Firm</span>
  <div class="contact-col address">
    <div>Post Office Box 4721</div>
    <div>Millbrook, SC 29555-4721</div>
  </div>
  <div class="col-divider" style="left:219px"></div>
  <div class="contact-col phones">
    <div class="row"><svg class="icon" viewBox="0 0 10 10"><path d="M2 1l2 2-1 1.5c.8 1.4 1.5 2.1 2.5 2.5L7 6l2 2-1.5 1.5C4.5 9 1 5.5.5 2.5z" fill="#d11f26"/></svg>(555) 214-3370</div>
    <div class="row"><svg class="icon" viewBox="0 0 10 10"><rect x="2.5" y="1" width="5" height="3" fill="none" stroke="#d11f26"/><rect x="1" y="4" width="8" height="4" fill="#d11f26"/></svg>(555) 214-5186</div>
  </div>
  <div class="col-divider" style="left:276px"></div>
  <div class="contact-col web">
    <div class="row"><svg class="icon" viewBox="0 0 10 10"><circle cx="5" cy="5" r="4" fill="none" stroke="#d11f26"/><path d="M1 5h8M5 1v8" stroke="#d11f26"/></svg>HarmClaimCounsel.example</div>
    <div class="row"><svg class="icon" viewBox="0 0 10 10"><circle cx="5" cy="5" r="4" fill="none" stroke="#d11f26"/><path d="M1 5h8M5 1v8" stroke="#d11f26"/></svg>PalmettoTrialAdvocates.example</div>
  </div>
  <div class="header-rule"></div>
</section>

<section class="sheet folder" aria-label="Presentation folder">
  <span class="wordmark">The Brandwell Firm</span>
</section>

<section class="sheet card-front" aria-label="Business card front">
  <span class="wordmark">The Brandwell Firm</span>
  <div class="name">Dana Whitlow</div>
  <div class="card-rule"></div>
  <div class="details">
    <div class="title">Attorney at Law</div>
    <div>Post Office Box 4721</div>
    <div>Millbrook, SC 29555-4721</div>
    <div class="gap">(555) 214-3370</div>
    <div>(555) 214-5186</div>
    <div>(888) 431-2059 <span class="red-text">(Toll-Free)</span></div>
    <div>HarmClaimCounsel.example</div>
    <div>PalmettoTrialAdvocates.example</div>
  </div>
</section>

<section class="sheet card-back" aria-label="Business card back">
  <span class="wordmark">The Brandwell Firm</span>
</section>

<section class="sheet envelope-front" aria-label="Envelope front">
  <span class="wordmark">The Brandwell Firm</span>
  <div class="return">
    <div>Post Office Box 4721</div>
    <div>Millbrook, SC 29555-4721</div>
  </div>
  <svg class="corner" width="150" height="150" viewBox="0 0 150 150" aria-hidden="true">
    <path d="M150 0 C150 80 90 150 10 150 L150 150 Z" fill="var(--red)"/>
  </svg>
</section>

<section class="sheet envelope-back" aria-label="Envelope back">
  <svg class="flap" width="428" height="70" viewBox="0 0 428 70" aria-hidden="true">
    <path d="M0 0 H428 L420 56 Q418 66 406 66 H22 Q10 66 8 56 Z" fill="var(--red)"/>
  </svg>
</section>

</body>
</html>
```